HALT THE CLAIMS

I'm virtually ready to launch my site, but I have a number of edits and modifications that need to be implemented. More importantly, I'm always looking to improve my site, particularly now that I am making my proverbial "FIRST IMPRESSION." Thus, I'm willing to see if there is someone who can add creativity and perhaps improve what I already have, particularly on the All Important Front Page.

```html
<!DOCTYPE html>
<html lang="en">
<head>
<meta charset="utf-8">
<title>Halt The Claims</title>
<link href="https://fonts.googleapis.com/css2?family=Montserrat:wght@800&family=Roboto:wght@400;500;700&display=swap" rel="stylesheet">
<style>
:root{
  --navy:#0b2250;
  --red:#a50016;
  --red-soft:#c63a4a;
  --white:#ffffff;
  --ink:#333a45;
  --gray:#5c6068;
  --line:#c9ccd2;
}
*{margin:0;padding:0;box-sizing:border-box}
html,body{width:1200px;height:3930px;overflow:hidden;background:var(--white)}
body{position:relative;font-family:'Roboto',sans-serif;color:var(--ink)}
.abs{position:absolute}
.shape{position:absolute;left:0;top:0}

/* header */
.topbar{left:0;top:0;width:1200px;height:82px;background:var(--white);z-index:3}
.brand-badge{left:146px;top:-6px;width:150px;height:150px;border-radius:50%;background:var(--white);z-index:4;display:flex;align-items:center;justify-content:center}
.brand-badge .disc{width:118px;height:118px;border-radius:50%;background:var(--red);display:flex;align-items:center;justify-content:center;text-align:center;color:var(--white);font-weight:700;font-size:15px;line-height:1.15}
.contact-item{display:flex;align-items:center;gap:16px;font-size:14px;line-height:20px;color:var(--ink);z-index:4}
.icon-dot{width:32px;height:32px;border-radius:50%;display:flex;align-items:center;justify-content:center;flex:none}
.icon-dot.navy{background:var(--navy)}
.icon-dot.red{background:var(--red)}
.main-nav{left:598px;top:72px;width:456px;height:34px;background:var(--navy);display:flex;align-items:center;z-index:4}
.main-nav a{color:var(--white);text-decoration:none;font-weight:700;font-size:15px;height:34px;line-height:34px;padding:0 18px}
.main-nav a.active{background:var(--red);padding:0 20px;width:93px}
.main-nav .search{margin-left:auto;margin-right:34px}

/* hero */
.hero-copy{left:178px;top:254px;width:414px;color:var(--white);font-weight:700;font-size:19px;line-height:24.6px;text-align:justify;text-align-last:center;z-index:2}
.hero-cta{left:180px;top:562px;width:410px;color:var(--white);font-weight:500;font-size:27px;line-height:33px;text-align:center;z-index:2}
.btn{display:flex;align-items:center;justify-content:center;font-weight:700;font-size:12.5px;text-transform:uppercase;z-index:2}
.btn-light{left:215px;top:695px;width:110px;height:36px;background:var(--white);color:var(--red)}
.btn-outline{left:333px;top:695px;width:222px;height:36px;border:2px solid var(--white);color:var(--white)}
.slider-dots span{position:absolute;left:0;width:7px;height:7px;border-radius:50%;background:var(--white)}

/* welcome */
.section-title{font-family:'Montserrat',sans-serif;font-weight:800;color:var(--navy);text-align:center;text-transform:uppercase}
.welcome-title{left:0;top:900px;width:1200px;font-size:48px;line-height:54px}
.col{width:385px;font-size:12.4px;line-height:27.3px;color:var(--gray);text-align:justify}
.col p+p{margin-top:13px}
.col p.tight{margin-top:0}
.team-photo{left:144px;top:1394px;width:911px;height:495px;background:linear-gradient(120deg,#34465e 0%,#8a8c8f 40%,#c9b9a2 70%,#e6dfd4 100%)}
.photo-btn{left:446px;top:1671px;width:307px;height:36px;background:var(--red);border:2px solid var(--white);color:var(--white);font-weight:500;font-size:12.5px;display:flex;align-items:center;justify-content:center;text-transform:uppercase}

/* services */
.services-title{left:0;top:1990px;width:1200px;font-size:46px;line-height:56px;color:var(--white)}
.services-lead{left:250px;top:2070px;width:700px;text-align:center;color:var(--white);font-size:16px;line-height:27px}
.service-label{width:230px;text-align:center;color:var(--white);font-weight:700;font-size:16px;line-height:23px;text-transform:uppercase}

/* faq */
.faq-title{left:0;top:2876px;width:1200px;font-size:47px;line-height:56px}
.faq-list{left:287px;top:2965px;width:626px;list-style:none}
.faq-list li{display:flex;align-items:center;justify-content:space-between;border-bottom:2px solid var(--line);font-size:17.5px;line-height:26px;color:var(--ink);padding:0 8px}
.faq-list li span{max-width:520px}
.chev{width:19px;height:19px;border-radius:50%;background:var(--red);flex:none;display:flex;align-items:center;justify-content:center}
.faq-answer{left:287px;top:3293px;width:626px;font-size:12.5px;line-height:26px;color:var(--gray)}

/* footer */
.foot-badge{left:504px;top:3450px;width:192px;height:192px;border-radius:50%;background:var(--white);display:flex;align-items:center;justify-content:center}
.foot-badge .disc{width:168px;height:168px;border-radius:50%;background:var(--red);display:flex;align-items:center;justify-content:center;text-align:center;color:var(--white);font-weight:700;font-size:22px;line-height:1.15}
.foot-contact{display:flex;align-items:center;gap:16px;color:var(--white);font-size:14px;line-height:20px}
.foot-contact .icon-dot{background:var(--white);width:34px;height:34px}
.foot-rule{left:0;top:3736px;width:1200px;height:1px;background:rgba(255,255,255,.2)}
.foot-nav{left:0;top:3766px;width:1200px;display:flex;justify-content:center;gap:0;color:var(--white);font-weight:700;font-size:15px}
.foot-nav span.sep{margin:0 22px}
.copyright{left:0;top:3814px;width:1200px;text-align:center;color:var(--white);font-size:14px}
.socials{left:528px;top:3860px;display:flex;gap:14px}
.socials span{width:40px;height:40px;border-radius:50%;background:var(--white)}
</style>
</head>
<body>

<!-- hero backdrop -->
<svg class="shape" width="1200" height="820" viewBox="0 0 1200 820" aria-hidden="false">
  <defs>
    <linearGradient id="heroPhoto" x1="0" y1="0" x2="1" y2="1">
      <stop offset="0" stop-color="#8a8f96"/>
      <stop offset="0.45" stop-color="#c7b6a4"/>
      <stop offset="1" stop-color="#e8e2da"/>
    </linearGradient>
    <linearGradient id="navyFade" x1="0" y1="0" x2="1" y2="0">
      <stop offset="0" stop-color="#0b2250"/>
      <stop offset="0.55" stop-color="#0b2250"/>
      <stop offset="1" stop-color="#0b2250" stop-opacity="0"/>
    </linearGradient>
  </defs>
  <path d="M0,82 H1200 V600 Q820,730 560,720 Q260,705 0,608 Z" fill="var(--navy)"/>
  <path d="M600,82 H1200 V600 Q820,730 600,718 Z" fill="url(#heroPhoto)" role="img" aria-label="Photo of a woman in glasses meeting with a client at a desk"/>
  <rect x="600" y="82" width="160" height="640" fill="url(#navyFade)"/>
  <path d="M0,608 Q260,705 560,720 Q820,730 1200,600 V616 Q820,744 560,736 Q260,722 0,622 Z" fill="var(--white)"/>
  <path d="M0,622 Q260,722 560,736 Q820,744 1200,616 V626 Q820,756 560,748 Q260,734 0,632 Z" fill="var(--navy)"/>
  <!-- hexagon panel -->
  <polygon points="18,489 198,171 580,171 738,489 580,806 198,806" fill="var(--red-soft)"/>
  <polygon points="30,489 206,182 572,182 726,489 572,795 206,795" fill="var(--red)"/>
  <polygon points="36,489 210,186 568,186 720,489 568,791 210,791" fill="none" stroke="var(--white)" stroke-width="2"/>
</svg>

<header class="abs topbar"></header>
<div class="abs brand-badge"><div class="disc">HALT THE<br>CLAIMS</div></div>

<div class="abs contact-item" style="left:473px;top:12px">
  <span class="icon-dot navy"><svg width="14" height="18" viewBox="0 0 14 18"><path d="M7 0C3 0 0 3 0 7c0 5 7 11 7 11s7-6 7-11c0-4-3-7-7-7zm0 9.5A2.5 2.5 0 1 1 7 4.5a2.5 2.5 0 0 1 0 5z" fill="#fff"/></svg></span>
  <span>4820 East Mesa Ridge Rd., Suite 210<br>Tempe, Arizona 85284</span>
</div>
<div class="abs contact-item" style="left:817px;top:18px">
  <span class="icon-dot red"><svg width="16" height="16" viewBox="0 0 16 16"><path d="M3.5 1l2.5 3-1.5 2c1 2 3 4 5 5l2-1.5 3 2.5-1.5 2.5C7 15 1 9 1 2.5z" fill="#fff"/></svg></span>
  <span>480.555.0142 / 800.555.0199</span>
</div>

<nav class="abs main-nav">
  <a class="active">HOME</a><a>ABOUT</a><a>CONTACT</a><a>PRODUCT</a>
  <svg class="search" width="16" height="16" viewBox="0 0 16 16"><circle cx="6.5" cy="6.5" r="5" fill="none" stroke="#fff" stroke-width="2"/><path d="M10.5 10.5L15 15" stroke="#fff" stroke-width="2"/></svg>
</nav>

<p class="abs hero-copy">BUSINESS OWNERS: Halt The Claims (HTC) Is An Extremely Affordable Legal Service Plan (As Little As $8.00 Per Month) That INSULATES Business Owners From Unwarranted LEGAL CLAIMS And Expensive LAWSUITS. Our Plan Uses Local, Experienced, Quality Attorneys Who Focus On PROBLEM PREVENTION Using Proprietary Tools Available Only To HTC Members. Contact Us For A Free Consultation And Receive A FREE OVERVIEW Of Your Business To See If You Are Truly Insulated From Legal Claims.</p>
<p class="abs hero-cta">Contact us to find out how<br>you can join us to HALT<br>THE CLAIMS!!</p>
<div class="abs btn btn-light">Learn More</div>
<div class="abs btn btn-outline">Schedule Free Consulation</div>
<div class="abs slider-dots" style="left:1144px;top:396px">
  <span style="top:0"></span><span style="top:15px;background:var(--red)"></span><span style="top:30px"></span>
</div>

<!-- welcome -->
<h1 class="abs section-title welcome-title">Welcome to<br>Halt the Claims</h1>
<div class="abs col" style="left:188px;top:1047px">
  <p>HTC is a group of attorney and legal assistants with many years of experience in litigation, who are devoted to PREVENTING LEGAL CLAIMS and COSTLY LAWSUITS through a variety of FREE and VERY AFFORDABLE services described below.OUR UNIQUE SERVICE PLAN MAKES IT POSSIBLE FOR US TO HALT THE CLAIMS.</p>
  <p>A homebuilding company was sued by a former employee who claimed to have been promised a more favorable sales area, which claim was disputed by the homebuilder. There was no evidence that such a promise had been made, other than the plaintiff's oral testimony. The company had the case dismissed, but spent $10,000 defending the case.</p>
</div>
<div class="abs col" style="left:628px;top:1047px">
  <p>And even though it was awarded its attorney's fees, the plaintiff proved uncollectible. Had the company been an HTC member, the case likely would never have been filed. Call for your FREE CONSULTATION and let us show you why the plaintiff likely would not have found a contingency attorney (as was the case) or been able to pay an attorney on an hourly basis. In short, by using HTC's services, the plaintiff's claim would not have been filed.</p>
  <p class="tight">In our vast experience with commercial litigation, we believe that a very large percentage of litigation cases hinge on "he said / she said" issues. By using HTC's services, we believe we can INSULATE you and your business from all such issues</p>
</div>

<div class="abs team-photo" role="img" aria-label="Photo of business people shaking hands across a meeting table"></div>
<div class="abs photo-btn">Contact us for a free consultation</div>

<!-- services -->
<svg class="shape" style="top:1907px" width="1200" height="890" viewBox="0 1907 1200 890">
  <polygon points="0,2275 206,1907 993,1907 1200,2275 901,2794 298,2794" fill="var(--red)"/>
  <polyline points="252,1907 42,2275 318,2754 882,2754 1158,2275 948,1907" fill="none" stroke="var(--white)" stroke-width="4"/>
  <defs>
    <linearGradient id="svcA" x1="0" y1="0" x2="1" y2="1"><stop offset="0" stop-color="#d9d6d1"/><stop offset="1" stop-color="#8d8f93"/></linearGradient>
    <linearGradient id="svcB" x1="0" y1="0" x2="1" y2="1"><stop offset="0" stop-color="#3a3c40"/><stop offset="1" stop-color="#e4e3e1"/></linearGradient>
    <linearGradient id="svcC" x1="0" y1="0" x2="1" y2="1"><stop offset="0" stop-color="#f2eee6"/><stop offset="1" stop-color="#b7b3ab"/></linearGradient>
  </defs>
  <polygon points="264,2257 318,2164 424,2164 478,2257 424,2350 318,2350" fill="url(#svcA)" role="img" aria-label="Photo of a contract being reviewed at a desk"/>
  <polygon points="492,2257 546,2164 652,2164 706,2257 652,2350 546,2350" fill="url(#svcB)" role="img" aria-label="Photo of a hand signing a document with a pen"/>
  <polygon points="719,2257 773,2164 879,2164 933,2257 879,2350 773,2350" fill="url(#svcC)" role="img" aria-label="Photo of a laptop on a bright office desk"/>
  <polygon points="264,2552 318,2459 424,2459 478,2552 424,2645 318,2645" fill="url(#svcC)" role="img" aria-label="Photo of a stressed businessman holding his head"/>
  <polygon points="492,2552 546,2459 652,2459 706,2552 652,2645 546,2645" fill="url(#svcA)" role="img" aria-label="Photo of two people exchanging legal papers"/>
  <polygon points="719,2552 773,2459 879,2459 933,2552 879,2645 773,2645" fill="url(#svcB)" role="img" aria-label="Photo of a person writing in a notebook"/>
</svg>
<h2 class="abs section-title services-title">Our Services</h2>
<p class="abs services-lead">The price for a membership is a ridiculously low $9.95 PER WEEK. We believe that this fee is very affordable. So what is it? Membership includes the following:</p>
<div class="abs service-label" style="left:256px;top:2368px">Free Initial<br>Consultation</div>
<div class="abs service-label" style="left:484px;top:2368px">Proprietary<br>Contract Language</div>
<div class="abs service-label" style="left:712px;top:2368px">Free<br>Consultation</div>
<div class="abs service-label" style="left:256px;top:2663px">Free Attorney<br>Letters</div>
<div class="abs service-label" style="left:484px;top:2663px">Litigation<br>Discounts</div>
<div class="abs service-label" style="left:712px;top:2663px">Collections</div>

<!-- faq -->
<h2 class="abs section-title faq-title">Frequently Asked Questions</h2>
<ul class="abs faq-list">
  <li style="height:52px"><span>Why should I be concerned about legal claims?</span><i class="chev"><svg width="9" height="9" viewBox="0 0 9 9"><path d="M3 1l3.5 3.5L3 8" fill="none" stroke="#fff" stroke-width="2"/></svg></i></li>
  <li style="height:58px"><span>Provide more details about the value of HTC's contract language.</span><i class="chev"><svg width="9" height="9" viewBox="0 0 9 9"><path d="M3 1l3.5 3.5L3 8" fill="none" stroke="#fff" stroke-width="2"/></svg></i></li>
  <li style="height:77px"><span>If I'm a contractor, for example, how can an HTC membership minimize legal claims against my business?</span><i class="chev"><svg width="9" height="9" viewBox="0 0 9 9"><path d="M3 1l3.5 3.5L3 8" fill="none" stroke="#fff" stroke-width="2"/></svg></i></li>
  <li style="height:56px"><span>What does an HTC membership cost?</span><i class="chev"><svg width="9" height="9" viewBox="0 0 9 9"><path d="M3 1l3.5 3.5L3 8" fill="none" stroke="#fff" stroke-width="2"/></svg></i></li>
  <li style="height:55px"><span>Do you have a Referral Program?</span><i class="chev"><svg width="9" height="9" viewBox="0 0 9 9"><path d="M1 6l3.5-3.5L8 6" fill="none" stroke="#fff" stroke-width="2"/></svg></i></li>
</ul>
<p class="abs faq-answer">Lorem ipsum dolor sit amet, consectetur adipiscing elit. Suspendisse varius enim in eros elementum tristique. Duis cursus, mi quis viverra ornare, eros dolor interdum nulla, ut commodo diam libero vitae erat. Aenean faucibus nibh et justo cursus id rutrum lorem i ut sem vitae risus tristique posuere.</p>

<!-- footer -->
<svg class="shape" style="top:3400px" width="1200" height="530" viewBox="0 3400 1200 530">
  <path d="M0,3512 Q600,3300 1200,3512 V3930 H0 Z" fill="var(--navy)"/>
  <path d="M0,3512 Q600,3300 1200,3512 V3528 Q600,3318 0,3528 Z" fill="var(--white)"/>
  <path d="M0,3498 Q600,3286 1200,3498 V3506 Q600,3294 0,3506 Z" fill="var(--navy)"/>
</svg>
<div class="abs foot-badge"><div class="disc">HALT THE<br>CLAIMS</div></div>
<div class="abs foot-contact" style="left:182px;top:3660px">
  <span class="icon-dot"><svg width="14" height="18" viewBox="0 0 14 18"><path d="M7 0C3 0 0 3 0 7c0 5 7 11 7 11s7-6 7-11c0-4-3-7-7-7zm0 9.5A2.5 2.5 0 1 1 7 4.5a2.5 2.5 0 0 1 0 5z" fill="#0b2250"/></svg></span>
  <span>4820 East Mesa Ridge Rd., Suite 210<br>Tempe, Arizona 85284</span>
</div>
<div class="abs foot-contact" style="left:514px;top:3660px">
  <span class="icon-dot"><svg width="16" height="16" viewBox="0 0 16 16"><path d="M3.5 1l2.5 3-1.5 2c1 2 3 4 5 5l2-1.5 3 2.5-1.5 2.5C7 15 1 9 1 2.5z" fill="#0b2250"/></svg></span>
  <span>480.555.0142 / 800.555.0199</span>
</div>
<div class="abs foot-contact" style="left:799px;top:3660px">
  <span class="icon-dot"><svg width="18" height="14" viewBox="0 0 18 14"><rect x="1" y="1" width="16" height="12" rx="2" fill="none" stroke="#0b2250" stroke-width="1.6"/><path d="M2 2l7 6 7-6" fill="none" stroke="#0b2250" stroke-width="1.6"/></svg></span>
  <span>www.halttheclaims.com</span>
</div>
<div class="abs foot-rule"></div>
<nav class="abs foot-nav">
  <span>HOME</span><span class="sep">/</span><span>ABOUT</span><span class="sep">/</span><span>SERVICES</span><span class="sep">/</span><span>FAQ</span><span class="sep">/</span><span>CONTACT US</span><span class="sep">/</span><span>TERMS OF SERVICE</span><span class="sep">/</span><span>PRIVACY POLICY</span>
</nav>
<p class="abs copyright">Copyright© 2023 Halttheclaims | All Rights Reserved &nbsp;|&nbsp; Privacy</p>
<div class="abs socials"><span aria-label="Social link"></span><span aria-label="Social link"></span><span aria-label="Social link"></span></div>

</body>
</html>
```